Marlow Vale Stud website

We would like to create a horse stud/agistment farm website similar to this websites we have attached below:
www.thornbeck.com.au
www.quillstead.com.au
www.brackley.com
www.pimsey.com.au
The main colour scheme are purple and white to align with the stable's racing colours.
We have also attach the company logo and also images of the farm and create some ideas for the website.
Many thanks for looking into this project!

```html
<!DOCTYPE html>
<html lang="en">
<head>
<meta charset="utf-8">
<title>Marlow Vale Stud</title>
<link rel="stylesheet" href="https://fonts.googleapis.com/css2?family=Libre+Baskerville&family=Lora:wght@400&family=Montserrat:wght@400;500;600&display=swap">
<style>
:root{
  --plum:#3d1443;
  --plum-deep:#35103b;
  --ink:#3a2a3d;
  --text:#4a4a4a;
  --white:#ffffff;
  --mist:#f3f2f3;
  --rule:#dcd6dd;
}
*{margin:0;padding:0;box-sizing:border-box}
html,body{width:1200px;height:2708px;overflow:hidden;background:var(--white)}
body{position:relative;font-family:"Lora",Georgia,serif;color:var(--text)}
.site-header{position:absolute;left:0;top:0;width:1200px;height:160px;background:var(--plum)}
.brand{position:absolute;left:60px;top:62px;color:var(--white);font-family:"Libre Baskerville",Georgia,serif;font-size:22px}
.social{position:absolute;display:flex;gap:22px}
.social span{width:16px;height:16px;border-radius:50%;background:rgba(255,255,255,.75)}
.site-header .social{right:56px;top:46px}
.main-nav{position:absolute;right:56px;top:112px;display:flex;gap:44px;font-family:"Montserrat",Arial,sans-serif;font-size:12px;font-weight:600;letter-spacing:1.5px;color:var(--white)}
.hero{position:absolute;left:0;top:160px;width:1200px;height:700px;background:linear-gradient(180deg,#2c2a33 0%,#5b4e56 30%,#8d8a86 52%,#d35f8a 66%,#3f7a2d 78%,#2f6a24 100%)}
.hero-dots{position:absolute;left:568px;top:812px;display:flex;gap:10px}
.hero-dots span{width:12px;height:12px;border-radius:50%;background:rgba(255,255,255,.55)}
.hero-dots span:first-child{background:var(--white)}
.intro{position:absolute;left:0;top:950px;width:1200px;text-align:center}
.intro-mark{display:inline-flex;align-items:center;gap:10px;font-family:"Libre Baskerville",Georgia,serif;font-size:20px;color:var(--plum)}
.intro-mark i{width:14px;height:14px;border-radius:50%;background:var(--plum);display:block}
.intro h1{margin-top:58px;font-family:"Libre Baskerville",Georgia,serif;font-weight:400;font-size:30px;color:var(--ink)}
.intro .tagline{margin-top:12px;font-family:"Montserrat",Arial,sans-serif;font-size:14px;letter-spacing:5px;color:#555}
.intro p{width:720px;margin:30px auto 0;font-size:12.5px;line-height:19px}
.btn{display:inline-block;background:var(--plum-deep);color:var(--white);font-family:"Montserrat",Arial,sans-serif;font-size:11px;font-weight:600;letter-spacing:2px;border-radius:22px;text-align:center}
.intro .btn{margin-top:34px;width:168px;height:42px;line-height:42px}
.divider{position:absolute;left:222px;top:1402px;width:756px;height:1px;background:var(--rule)}
.photo{position:absolute}
.photo-paddock{left:222px;top:1424px;width:372px;height:276px;background:linear-gradient(180deg,#4f86c8 0%,#a7c6e4 45%,#4b3b2c 62%,#4f8f36 100%)}
.photo-fence{left:610px;top:1424px;width:372px;height:276px;background:linear-gradient(180deg,#6b86a6 0%,#b8c4cf 40%,#7d9a4a 60%,#3f6b2a 100%)}
.photo-aerial{left:182px;top:1720px;width:594px;height:340px;background:linear-gradient(180deg,#5a96d8 0%,#c9dff0 22%,#7fa35a 40%,#4f8a34 70%,#6b8e4a 100%)}
.facilities{position:absolute;left:812px;top:1740px;width:196px}
.facilities h2,.news h2{font-family:"Libre Baskerville",Georgia,serif;font-weight:400;font-size:30px;color:var(--ink)}
.facilities p{margin-top:22px;font-size:12.5px;line-height:18px}
.news-band{position:absolute;left:0;top:2120px;width:1200px;height:452px;background:var(--mist)}
.news-photo{position:absolute;left:258px;top:2220px;width:240px;height:240px;border-radius:50%;background:radial-gradient(circle at 50% 40%,#8a7f86 0%,#4a2f55 45%,#3f7a2d 85%)}
.news{position:absolute;left:560px;top:2228px;width:448px}
.news p{margin-top:20px;font-size:12.5px;line-height:18px}
.news-band .btn{position:absolute;left:818px;top:2422px;width:190px;height:44px;line-height:44px}
.site-footer{position:absolute;left:0;top:2572px;width:1200px;height:136px;background:var(--plum);color:var(--white);font-size:12px;line-height:20px}
.footer-contact{position:absolute;left:232px;top:28px}
.footer-links{position:absolute;left:600px;top:28px}
.site-footer .social{left:900px;top:34px}
.copyright{position:absolute;left:880px;top:92px;font-family:"Montserrat",Arial,sans-serif;font-size:10px}
</style>
</head>
<body>
<header class="site-header">
  <div class="brand">Marlow Vale Stud</div>
  <div class="social"><span></span><span></span><span></span></div>
  <nav class="main-nav"><span>HOME</span><span>STALLIONS</span><span>BROOM MARES</span><span>ABOUT THE FARM</span><span>CONTACT</span></nav>
</header>

<div class="hero" role="img" aria-label="Grey racehorse galloping on turf with a jockey in purple and white silks, flower beds behind"></div>
<div class="hero-dots"><span></span><span></span></div>

<section class="intro">
  <div class="intro-mark"><i></i>Marlow Vale Stud</div>
  <h1>MV stallions, distinguished by excellence</h1>
  <div class="tagline">MARLOW VALE STUD</div>
  <p>Bred on rolling pasture and raised with patience, our stallions carry proven bloodlines and sound temperaments. Every horse on the farm receives daily care from a small, experienced team who know each animal by name. Visit the stud to meet the stallions, walk the paddocks and see why breeders return season after season to build their next champion with us.</p>
  <span class="btn">LEARN MORE</span>
</section>

<div class="divider"></div>

<div class="photo photo-paddock" role="img" aria-label="Group of dark horses standing in a paddock under a blue sky"></div>
<div class="photo photo-fence" role="img" aria-label="Green paddock with timber fencing and trees"></div>
<div class="photo photo-aerial" role="img" aria-label="Aerial view of the farm buildings among green hills"></div>

<section class="facilities">
  <h2>Facilities</h2>
  <p>The farm spans green valley paddocks with sheltered yards, a modern foaling unit and spacious stables. Mares and foals enjoy quiet grazing, clean water and shade through every season. Our agistment clients have access to round yards, a covered arena and a veterinary room on site, all kept by staff who live on the property.</p>
</section>

<section class="news-band">
  <span class="btn">LEARN MORE</span>
</section>
<div class="news-photo" role="img" aria-label="Racehorse and jockey in purple silks crossing the finish"></div>
<section class="news">
  <h2>News</h2>
  <p>Our grey filly stormed home in the feature race on Saturday, giving the farm its third winner of the spring. Two new mares have arrived for the breeding season and the first foals are due next month. Follow our news for race results, sales updates and life on the farm.</p>
</section>

<footer class="site-footer">
  <div class="footer-contact">Marlow Vale Stud<br>Ashgrove,<br>Phone: +61 455 218 730</div>
  <div class="footer-links">Stallions<br>Stud<br>News</div>
  <div class="social"><span></span><span></span><span></span></div>
  <div class="copyright">© 2017 MV Stud All rights reserved</div>
</footer>
</body>
</html>
```